Brightbay Orthodontics business card design

Need a business card design that reflects our re-branding (orthodontic office - braces) and a new partnership with a pediatric dental office. We would like to include "for adults and children" on the card as well so adults know they are welcome to get their braces here as well. Office design is modern and would like business card to reflect a modern type look. Here's the text we would like to be included on the card:

Darren Wolcott, DDS, MSD
5214 West Linden Avenue, Suite 204
Alderton, WA 76991
555-418-2637
www.brightbayortho.example
info@brightbayortho.example

Can we add the following to the existing designs? Darren Wolcott, DDS, MSD 5214 West Linden Avenue, Suite 204 Alderton, WA 76991 555-418-2637

Does anyone have any more vertical designs available? Thanks!

Dental

```html
<!DOCTYPE html>
<html lang="en">
<head>
<meta charset="utf-8">
<title>Brightbay Orthodontics – Business Card</title>
<link href="https://fonts.googleapis.com/css2?family=Lato:wght@300;400;700;900&display=swap" rel="stylesheet">
<style>
  :root{
    --bg:#e6e4df;
    --card:#fbfbfb;
    --ink:#3b3b3b;
    --muted:#8a8a8a;
    --faint:#e9e9e9;
    --line:#555555;
    --yellow:#f2e51c;
    --blue:#1fa0d8;
    --magenta:#e0219a;
    --green:#8cc63f;
    --orange:#f5a623;
    --black:#1e1e1e;
  }
  *{box-sizing:border-box;margin:0;padding:0}
  html,body{width:759px;height:1200px;overflow:hidden}
  body{background:var(--bg);font-family:'Lato',sans-serif;color:var(--ink);position:relative}

  .card{position:absolute;top:320px;width:320px;height:560px;background:var(--card);
        border-radius:6px;overflow:hidden;box-shadow:0 6px 18px rgba(0,0,0,.15)}
  .card--front{left:40px}
  .card--back{left:399px}

  /* colour tabs */
  .tabs{position:absolute;display:flex;gap:3px}
  .tabs span{flex:1}
  .tabs--top{top:0;left:0;right:0;height:18px;padding-left:40px}
  .tabs--top span{border-radius:0 0 6px 6px}
  .tabs--bottom{bottom:0;left:0;right:0;height:22px;padding-right:40px}
  .tabs--bottom span{border-radius:6px 6px 0 0}
  .t-yellow{background:var(--yellow)} .t-blue{background:var(--blue)}
  .t-magenta{background:var(--magenta)} .t-green{background:var(--green)}
  .t-orange{background:var(--orange)} .t-black{background:var(--black)}

  /* front */
  .doctor{position:absolute;top:52px;right:28px;text-align:right}
  .doctor__name{font-weight:300;font-size:22px;letter-spacing:1.5px;color:#555}
  .doctor__title{font-weight:300;font-size:13px;letter-spacing:1px;color:var(--muted);margin-top:2px}

  .brand{position:absolute;top:118px;left:28px;right:28px;display:flex;align-items:center;gap:12px}
  .brand__dot{width:34px;height:34px;border-radius:50%;background:var(--blue);flex:none}
  .brand__name{font-weight:900;font-size:30px;line-height:1.05;color:var(--ink)}

  .contact{position:absolute;left:28px;right:28px;top:226px}
  .contact__row{position:relative;height:60px}
  .contact__row + .contact__row{margin-top:14px}
  .contact__text{position:absolute;left:0;right:40px;bottom:8px;font-size:11.5px;line-height:1.45;color:#666;letter-spacing:.3px}
  .contact__rule{position:absolute;left:0;right:0;bottom:0;height:1.5px}
  .contact__icon{position:absolute;right:0;bottom:-28px;width:28px;height:28px;display:flex;align-items:center;justify-content:center}
  .row--phone .contact__rule,.row--phone .contact__icon{background:var(--blue)}
  .row--web .contact__rule,.row--web .contact__icon{background:var(--magenta)}
  .row--address .contact__rule,.row--address .contact__icon{background:var(--green)}

  .tagline{position:absolute;left:28px;right:28px;top:470px;font-size:13px;letter-spacing:3px;color:#555}

  /* back: laid out landscape, turned to stand upright */
  .back-face{position:absolute;left:0;top:0;width:560px;height:320px;transform-origin:0 0;transform:translate(320px,0) rotate(90deg)}
  .watermark{position:absolute;left:150px;top:22px;font-weight:900;font-size:40px;line-height:1.05;color:var(--faint)}
  .tabs--side{top:0;bottom:0;right:0;width:24px;flex-direction:column;padding-top:30px}
  .tabs--side span{border-radius:6px 0 0 6px}
  .appt-pill{position:absolute;left:26px;top:258px;background:var(--blue);color:#fff;font-weight:700;font-size:15px;
             padding:8px 22px;border-radius:20px;letter-spacing:.3px}
  .appt-label{position:absolute;left:250px;top:142px;font-size:11px;color:#b5b5b5;letter-spacing:.5px}
  .field{position:absolute;left:250px;right:64px;height:1.5px;background:var(--line)}
  .field--date{top:192px}
  .field--time{top:240px}
  .field-label{position:absolute;font-size:12px;color:#444}
  .fl-date{left:205px;top:182px}
  .fl-time{left:205px;top:230px}
  .fl-pm{left:470px;top:174px}
  .fl-am{left:470px;top:222px}
</style>
</head>
<body>

<section class="card card--front" aria-label="Business card front">
  <div class="tabs tabs--top">
    <span class="t-yellow"></span><span class="t-blue"></span><span class="t-magenta"></span>
    <span class="t-green"></span><span class="t-orange"></span><span class="t-black"></span>
  </div>

  <div class="doctor">
    <p class="doctor__name">Darren Wolcott</p>
    <p class="doctor__title">DDS, MSD</p>
  </div>

  <div class="brand">
    <span class="brand__dot"></span>
    <p class="brand__name">Brightbay<br>Orthodontics</p>
  </div>

  <div class="contact">
    <div class="contact__row row--phone">
      <p class="contact__text">555-418-2637</p>
      <span class="contact__rule"></span>
      <span class="contact__icon">
        <svg width="16" height="16" viewBox="0 0 24 24"><path fill="#fff" d="M6.6 10.8a15 15 0 0 0 6.6 6.6l2.2-2.2c.3-.3.7-.4 1-.2 1.1.4 2.3.6 3.6.6.6 0 1 .4 1 1V20c0 .6-.4 1-1 1A17 17 0 0 1 3 4c0-.6.4-1 1-1h3.5c.6 0 1 .4 1 1 0 1.3.2 2.5.6 3.6.1.3 0 .7-.2 1z"/></svg>
      </span>
    </div>
    <div class="contact__row row--web">
      <p class="contact__text">www.brightbayortho.example<br>info@brightbayortho.example</p>
      <span class="contact__rule"></span>
      <span class="contact__icon">
        <svg width="16" height="16" viewBox="0 0 24 24"><rect x="2" y="4" width="20" height="13" rx="1" fill="none" stroke="#fff" stroke-width="2"/><path d="M8 21h8M12 17v4" stroke="#fff" stroke-width="2"/></svg>
      </span>
    </div>
    <div class="contact__row row--address">
      <p class="contact__text">5214 West Linden Avenue,<br>Suite 204 Alderton, WA 76991</p>
      <span class="contact__rule"></span>
      <span class="contact__icon">
        <svg width="16" height="16" viewBox="0 0 24 24"><path fill="#fff" d="M12 3 2 12h3v8h5v-5h4v5h5v-8h3z"/></svg>
      </span>
    </div>
  </div>

  <p class="tagline">FOR ADULTS &amp; CHILDREN</p>

  <div class="tabs tabs--bottom">
    <span class="t-yellow"></span><span class="t-blue"></span><span class="t-magenta"></span>
    <span class="t-green"></span><span class="t-orange"></span><span class="t-black"></span>
  </div>
</section>

<section class="card card--back" aria-label="Business card back, appointment card">
  <div class="back-face">
    <p class="watermark">Brightbay<br>Orthodontics</p>
    <p class="appt-label">Next Appointment</p>
    <span class="field-label fl-date">Date:</span>
    <span class="field field--date"></span>
    <span class="field-label fl-pm">PM</span>
    <span class="field-label fl-time">Time:</span>
    <span class="field field--time"></span>
    <span class="field-label fl-am">AM</span>
    <p class="appt-pill">Appointment Card</p>
    <div class="tabs tabs--side">
      <span class="t-black"></span><span class="t-orange"></span><span class="t-green"></span>
      <span class="t-magenta"></span><span class="t-blue"></span><span class="t-yellow"></span>
    </div>
  </div>
</section>

</body>
</html>
```